Budget Brand Responsive Website

Flat vector style website needed for value based IT support company. looking for clean, illustration intensive based design. Current test site can be found at www.bright-mend.co.uk and holding page it www.brightmend.co.uk this will show text and services, please feel free to use placeholder text if you think we need alternative text in places. Emphasis should be on low cost support and services listed on the site, would be nice to see costs in bold images. important colors are the blue, orange and white, see holding page and attached image of an advert

It Company

```html
<!DOCTYPE html>
<html lang="en">
<head>
<meta charset="utf-8">
<title>Bright Mend – IT Support</title>
<link href="https://fonts.googleapis.com/css2?family=Open+Sans:wght@400;600;700;800&display=swap" rel="stylesheet">
<style>
:root{
  --blue:#3a5a9c;
  --blue-dark:#2b4275;
  --navy:#26385f;
  --orange:#f07a1a;
  --ink:#2e2e2e;
  --muted:#7a7a7a;
  --line:#d7d9de;
  --soft:#f1f2f4;
  --purple:#5a3c8e;
  --sky:#2f8fd6;
  --gold:#f2a81c;
  --green:#6aa829;
  --white:#ffffff;
}
*{box-sizing:border-box;margin:0;padding:0}
html,body{width:1200px;height:2752px;overflow:hidden}
body{font-family:"Open Sans",Arial,sans-serif;color:var(--ink);background:var(--white);position:relative}

/* header + hero */
.hero{position:absolute;left:0;top:0;width:1200px;height:720px;
  background:linear-gradient(180deg,#eef2f7 0%,#dfe6ef 55%,#c9d3e0 100%)}
.hero-photo{position:absolute;inset:0}
.site-header{position:absolute;left:0;top:0;width:1200px;height:120px;display:flex;align-items:center;justify-content:space-between;padding:0 80px 0 100px}
.brand{display:flex;align-items:center;gap:14px;font-weight:800;font-size:34px;color:var(--blue-dark);letter-spacing:1px}
.brand-mark{width:28px;height:28px;background:var(--orange)}
.nav{display:flex;gap:6px}
.nav a{font-size:15px;font-weight:600;color:var(--blue-dark);text-decoration:none;padding:8px 16px;text-transform:uppercase}
.nav a.active{background:var(--white);border:1px solid var(--line)}
.slider-dots{position:absolute;left:50%;top:628px;transform:translateX(-50%);display:flex;gap:10px}
.slider-dots span{width:14px;height:14px;border-radius:50%;background:#9aa7b9}
.slider-dots span.on{background:var(--orange)}

/* headings */
.section-title{text-align:center;font-size:28px;font-weight:700;text-transform:uppercase;color:var(--ink)}
.section-title em{font-style:normal;color:var(--orange)}
.title-rule{width:60px;height:3px;background:var(--line);margin:14px auto 0}

/* services */
.services{position:absolute;top:730px;left:0;width:1200px;height:358px;padding-top:20px}
.service-grid{display:grid;grid-template-columns:repeat(3,320px);column-gap:40px;row-gap:44px;margin:46px 0 0 120px}
.service{display:flex;gap:18px}
.service-icon{width:48px;height:48px;border-radius:50%;border:2px solid var(--line);flex:none;display:flex;align-items:center;justify-content:center}
.service h3{font-size:15px;font-weight:700;text-transform:uppercase;margin-bottom:6px}
.service li{list-style:none;font-size:12px;color:var(--muted);line-height:20px}
.service li::before{content:"• ";color:var(--orange)}

/* call band */
.call-band{position:absolute;top:1088px;left:0;width:1200px;height:292px;background:linear-gradient(90deg,var(--blue-dark),var(--blue));color:var(--white)}
.call-text{position:absolute;left:100px;top:44px;width:780px;font-size:14px;line-height:24px;opacity:.92}
.call-sub{position:absolute;left:100px;top:170px;font-size:14px;opacity:.9}
.call-phone{position:absolute;left:100px;top:196px;font-size:30px;font-weight:600}
.call-phone strong{font-weight:800;margin-left:8px}
.call-photo{position:absolute;right:0;top:0;width:300px;height:292px;background:linear-gradient(135deg,#c7d3e6,#8ea3c6)}

/* pricing */
.pricing{position:absolute;top:1380px;left:0;width:1200px;height:532px;padding-top:52px}
.plans{position:absolute;top:138px;left:168px;display:flex;gap:10px;align-items:flex-start}
.plan{width:206px;background:var(--soft);border:1px solid var(--line);box-shadow:0 3px 8px rgba(0,0,0,.12);text-align:left}
.plan-head{height:72px;display:flex;align-items:center;justify-content:center;color:var(--white);font-size:24px;font-weight:800;text-transform:uppercase;letter-spacing:1px}
.plan-body{padding:18px 18px 22px;height:288px;position:relative}
.plan-lead{font-size:10px;font-weight:700;text-transform:uppercase;margin-bottom:12px;white-space:nowrap}
.plan-row{font-size:12px;color:#555;line-height:26px;border-bottom:1px solid #e1e3e7;white-space:nowrap}
.plan-row b{margin-left:6px}
.order{position:absolute;left:50%;bottom:22px;transform:translateX(-50%);background:var(--green);color:var(--white);font-size:12px;font-weight:700;padding:10px 22px;text-transform:uppercase;white-space:nowrap}
.plan.support .plan-head{background:var(--purple)}
.plan.voice .plan-head{background:var(--orange)}
.plan.cloud .plan-head{background:var(--gold)}
.plan.hosting{width:220px;margin-top:-18px;position:relative}
.plan.hosting .plan-head{background:var(--sky);height:84px}
.plan.hosting .plan-body{height:320px;background:var(--white)}
.plan-badge{position:absolute;left:-10px;top:-14px;width:40px;height:40px;border-radius:50%;background:var(--gold)}

/* about */
.about{position:absolute;top:1912px;left:0;width:1200px;height:360px;background:var(--blue);color:var(--white)}
.about-photo{position:absolute;left:120px;top:28px;width:380px;height:304px;background:linear-gradient(135deg,#dfe4ec,#9fb0c9)}
.about-copy{position:absolute;left:540px;top:44px;width:540px}
.about-copy h2{font-size:26px;font-weight:700;text-transform:uppercase;margin-bottom:14px}
.about-copy p{font-size:13px;line-height:22px;opacity:.92}
.read-more{display:inline-block;margin-top:22px;background:var(--white);color:var(--blue-dark);font-size:13px;padding:8px 18px}

/* contact */
.contact{position:absolute;top:2272px;left:0;width:1200px;height:376px}
.contact h2{position:absolute;left:120px;top:38px;font-size:26px;font-weight:700;text-transform:uppercase}
.contact h2 em{font-style:normal;color:var(--orange)}
.contact-form{position:absolute;left:120px;top:100px;display:grid;grid-template-columns:460px 460px;column-gap:40px;row-gap:16px}
.field{height:42px;border:1px solid var(--line);font-size:12px;color:#666;padding:12px 14px}
.field.message{height:100px;grid-row:span 2}
.send{width:80px;height:34px;background:var(--orange);color:var(--white);font-size:12px;font-weight:700;display:flex;align-items:center;justify-content:center}

/* footer */
.site-footer{position:absolute;top:2648px;left:0;width:1200px;height:104px;background:var(--navy);color:#c9d2e4;font-size:13px;display:flex;align-items:center;padding:0 120px}
</style>
</head>
<body>

<section class="hero">
  <div class="hero-photo" role="img" aria-label="Office team of smiling colleagues gathered around a laptop"></div>
  <header class="site-header">
    <div class="brand"><span class="brand-mark"></span>BRIGHT MEND</div>
    <nav class="nav">
      <a class="active" href="#">Home</a><a href="#">Support</a><a href="#">Services</a><a href="#">About</a><a href="#">Contact Us</a>
    </nav>
  </header>
  <div class="slider-dots"><span class="on"></span><span></span><span></span><span></span></div>
</section>

<section class="services">
  <h2 class="section-title">Services &amp; Benefits of <em>Bright Mend</em></h2>
  <div class="title-rule"></div>
  <div class="service-grid">
    <div class="service"><div class="service-icon"><svg width="22" height="22" viewBox="0 0 22 22"><circle cx="11" cy="11" r="8" fill="none" stroke="#9a9a9a" stroke-width="2"/></svg></div>
      <div><h3>Support</h3><ul><li>Unlimited remote support</li><li>Monitoring and maintenance</li><li>Affordable fixed monthly</li></ul></div></div>
    <div class="service"><div class="service-icon"><svg width="22" height="22" viewBox="0 0 22 22"><path d="M6 3h4l1 5-3 2a11 11 0 0 0 4 4l2-3 5 1v4c0 1-1 2-2 2A15 15 0 0 1 4 5c0-1 1-2 2-2z" fill="#9a9a9a"/></svg></div>
      <div><h3>Voice</h3><ul><li>VoIP telephone systems</li><li>Telephone lines</li><li>Call routing and more</li></ul></div></div>
    <div class="service"><div class="service-icon"><svg width="22" height="22" viewBox="0 0 22 22"><circle cx="11" cy="11" r="8" fill="none" stroke="#9a9a9a" stroke-width="2"/><path d="M3 11h16M11 3v16" stroke="#9a9a9a" stroke-width="2"/></svg></div>
      <div><h3>Internet</h3><ul><li>Business broadband</li><li>Leased lines</li><li>Fibre broadband</li></ul></div></div>
    <div class="service"><div class="service-icon"><svg width="22" height="22" viewBox="0 0 22 22"><rect x="5" y="10" width="12" height="9" fill="#9a9a9a"/><path d="M7 10V7a4 4 0 0 1 8 0v3" fill="none" stroke="#9a9a9a" stroke-width="2"/></svg></div>
      <div><h3>Security</h3><ul><li>Encryption</li><li>Antivirus and firewalls</li><li>Patch management</li></ul></div></div>
    <div class="service"><div class="service-icon"><svg width="22" height="22" viewBox="0 0 22 22"><rect x="4" y="4" width="14" height="5" fill="#9a9a9a"/><rect x="4" y="12" width="14" height="5" fill="#9a9a9a"/></svg></div>
      <div><h3>Hosting</h3><ul><li>Hosted exchange</li><li>Web hosting</li><li>Email protection</li></ul></div></div>
    <div class="service"><div class="service-icon"><svg width="22" height="22" viewBox="0 0 22 22"><path d="M6 16h11a4 4 0 0 0 0-8 6 6 0 0 0-11 1 4 4 0 0 0 0 7z" fill="#9a9a9a"/></svg></div>
      <div><h3>Cloud</h3><ul><li>Backup and DR</li><li>Virtual desktops</li><li>Virtual servers</li></ul></div></div>
  </div>
</section>

<section class="call-band">
  <p class="call-text">We don't believe any local business should pay for IT Support you don't need. You shouldn't be overcharged just for cover you're not using the latest technology. If you're not happy with the service you're getting from your provider, you should be free to walk away. As a local business ourselves, we do it how it should be done.</p>
  <p class="call-sub">Want to learn how other businesses are profiting from Bright Mend?</p>
  <p class="call-phone">Call us today on <strong>01632 960 222</strong></p>
  <div class="call-photo" role="img" aria-label="Smiling support agent wearing a headset"></div>
</section>

<section class="pricing">
  <h2 class="section-title">Pricing for our most <em>popular services</em></h2>
  <div class="title-rule"></div>
  <div class="plans">
    <div class="plan support"><div class="plan-head">Support</div><div class="plan-body">
      <p class="plan-lead">Unlimited monthly support</p>
      <p class="plan-row">Workstation: <b>£8.50</b></p><p class="plan-row">Thin Client:<b>£20.00</b></p><p class="plan-row">Server: <b>£45.00</b></p><p class="plan-row">Laptop: <b>£10.00</b></p><p class="plan-row">Network: <b>£20.00</b></p>
      <span class="order">Order now</span></div></div>
    <div class="plan voice"><div class="plan-head">Voice</div><div class="plan-body">
      <p class="plan-lead">Lower rates: call charges</p>
      <p class="plan-row">Local: <b>£0.01</b></p><p class="plan-row">National: <b>£0.02</b></p><p class="plan-row">Mobile: <b>£0.05</b></p><p class="plan-row">Line: <b>£10.00</b></p><p class="plan-row">Handset: <b>£20.00</b></p>
      <span class="order">Order now</span></div></div>
    <div class="plan hosting"><span class="plan-badge"></span><div class="plan-head">Hosting</div><div class="plan-body">
      <p class="plan-lead">Features</p>
      <p class="plan-row">Monthly Bandwidth</p><p class="plan-row">Dedicated Web Space</p><p class="plan-row">Shared or Cloud</p><p class="plan-row">Free Email Manager</p><p class="plan-row">Online Support Tools</p>
      <span class="order">Order now</span></div></div>
    <div class="plan cloud"><div class="plan-head">Cloud</div><div class="plan-body">
      <p class="plan-lead">Increase performance</p>
      <p class="plan-row">Workstation: <b>£8.50</b></p><p class="plan-row">Thin Client:<b>£20.00</b></p><p class="plan-row">Server: <b>£45.00</b></p><p class="plan-row">Storage: <b>£10.00</b></p><p class="plan-row">Backup: <b>£20.00</b></p>
      <span class="order">Order now</span></div></div>
  </div>
</section>

<section class="about">
  <div class="about-photo" role="img" aria-label="Business team meeting around a laptop"></div>
  <div class="about-copy">
    <h2>About Us</h2>
    <p>Bright Mend is a market leading Managed Service Provider (MSP). With years of industry experience, we commit to delivering leading technologies combined with a focus on quality service delivery. We have one of the most critical success factors in our continued and healthy growth: a broad portfolio of Support Services and Product offerings that meets the demands of our client base. We have maintained the proactive and flexible approach which first attracted many of our loyal clients and has continued.</p>
    <span class="read-more">Read More</span>
  </div>
</section>

<section class="contact">
  <h2>Contact us <em>form</em></h2>
  <div class="contact-form">
    <div class="field">First Name</div><div class="field">Last Name</div>
    <div class="field">Email</div><div class="field">Password</div>
    <div class="field">Your Phone Number</div><div class="field message">Message</div>
    <div class="send">SEND</div>
  </div>
</section>

<footer class="site-footer">© 2015 Bright Mend. All Rights Reserved</footer>

</body>
</html>
```